USB Flash Drive Catalogue

I would like to make a paper catalogue of the products from our Crafterly store. There are currently 209 items on Crafterly. Some would be excluded. The listings have pricing and would need to be organized a bit different but all the information is there.

https://www.crafterly.com/shop/TurboStickHub/items?ref=pagination&page=1

```html
<!DOCTYPE html>
<html lang="en">
<head>
<meta charset="utf-8">
<title>Product Catalog – TurboStickHub</title>
<link rel="stylesheet" href="https://fonts.googleapis.com/css2?family=Montserrat:wght@400;600;700;800&display=swap">
<style>
  :root {
    --orange: #e8823a;
    --grey: #5f6062;
    --frame: #6b6c6e;
    --paper: #f4f4f2;
    --ink: #3a3b3d;
    --backdrop: #d9d9d7;
    --white: #ffffff;
  }
  * { box-sizing: border-box; margin: 0; padding: 0; }
  html, body {
    width: 1200px; height: 804px; overflow: hidden;
    background: var(--backdrop);
    font-family: "Montserrat", sans-serif;
  }
  .cover {
    position: absolute; left: 338px; top: 32px;
    width: 523px; height: 740px;
    background: var(--orange);
    box-shadow: 0 10px 30px rgba(0,0,0,.25);
    overflow: hidden;
  }
  .cover-shapes { position: absolute; inset: 0; }
  .title-block { position: absolute; left: 52px; top: 92px; color: var(--white); }
  .title-kicker { font-size: 27px; font-weight: 800; line-height: 1; letter-spacing: .5px; }
  .title-main { font-size: 60px; font-weight: 800; line-height: .95; letter-spacing: 1px; text-shadow: 0 3px 6px rgba(0,0,0,.25); }
  .headline { margin-top: 8px; font-size: 14.5px; font-weight: 600; letter-spacing: .6px; }
  .intro { margin-top: 16px; width: 250px; font-size: 8.5px; line-height: 1.5; font-weight: 400; opacity: .9; }
  .product-photo {
    position: absolute;
    border: 4px solid var(--frame);
    background: var(--white);
    padding: 6px;
  }
  .product-photo .fill { width: 100%; height: 100%; }
  .photo-maple { left: 62px; top: 290px; width: 150px; height: 120px; }
  .photo-maple .fill { background: radial-gradient(circle at 50% 55%, #d9b56a, #efe5cd 70%); }
  .photo-white { left: 92px; top: 418px; width: 140px; height: 118px; }
  .photo-white .fill { background: radial-gradient(circle at 50% 55%, #e2ddd8, #f6f5f3 70%); }
  .photo-walnut { left: 222px; top: 262px; width: 168px; height: 148px; }
  .photo-walnut .fill { background: radial-gradient(circle at 50% 50%, #7a4a2c, #e9e4df 75%); }
  .brand { position: absolute; left: 52px; top: 624px; display: flex; align-items: center; gap: 9px; }
  .brand-dot { width: 20px; height: 20px; border-radius: 50%; background: var(--orange); }
  .brand-name { font-size: 19px; font-weight: 700; letter-spacing: 2px; color: var(--ink); }
  .contact { position: absolute; left: 52px; top: 672px; font-size: 10px; font-weight: 700; line-height: 1.5; }
  .contact-email { color: var(--ink); }
  .contact-web { color: var(--orange); font-size: 11px; }
</style>
</head>
<body>
  <article class="cover">
    <svg class="cover-shapes" width="523" height="740" viewBox="0 0 523 740" aria-hidden="true">
      <polygon points="0,585 523,468 523,706 230,562 0,600" fill="var(--grey)"/>
      <polygon points="0,600 230,562 523,706 523,740 0,740" fill="var(--paper)"/>
    </svg>

    <header class="title-block">
      <p class="title-kicker">PRODUCT</p>
      <h1 class="title-main">CATALOG</h1>
      <p class="headline">YOUR HEADLINE GOES HERE</p>
      <p class="intro">Browse our wooden and crystal flash drive boxes, engraved gift sets and custom keepsakes for every occasion and celebration.</p>
    </header>

    <figure class="product-photo photo-maple">
      <div class="fill" role="img" aria-label="Engraved maple wood USB gift box"></div>
    </figure>
    <figure class="product-photo photo-walnut">
      <div class="fill" role="img" aria-label="Engraved walnut wood box with matching wooden USB drive"></div>
    </figure>
    <figure class="product-photo photo-white">
      <div class="fill" role="img" aria-label="White gift box with personalised lettering and USB drive"></div>
    </figure>

    <div class="brand">
      <span class="brand-dot"></span>
      <span class="brand-name">TURBOSTICKHUB</span>
    </div>

    <footer class="contact">
      <p class="contact-email">Email: info@turbostickhub-shop.com</p>
      <p class="contact-web">WWW.TURBOSTICKHUB-SHOP.COM</p>
    </footer>
  </article>
</body>
</html>
```